FinTech company looking to revamp and expand client-facing interface for our financial models

Pellworth Engines currently has a very simple website that allows clients to interact with our financial models. We are looking to completely redesign the current site and add several extra pages to provide extra functionality. We want the design to have a modern, slick feel, that will work on both a desktop or a tablet. It should be straightforward for clients to move between different pages at any time, and clear from the layout how to interact with the more advanced features. We have included screenshots of existing pages in the attached design brief, as well as sketches of the functionality required by the new pages, but can't provide a direct link to the current site.
Target Market(s)
Professional investors that will be paying to access the interface
Industry/Entity Type
Finance
Number of Pages Required
4 page
Colors
Designer to choose colors to be used in the design.
Look and feel
Each slider illustrates characteristics of the customer's brand and the style your logo design should communicate.

```html
<!DOCTYPE html>
<html lang="en">
<head>
<meta charset="utf-8">
<title>Pellworth Engines – Model Dashboard</title>
<link rel="stylesheet" href="https://fonts.googleapis.com/css2?family=Roboto:wght@400;500;700&display=swap">
<style>
  :root {
    --stage: #9aa5d6;
    --navy: #044d7a;
    --lime: #a9cc3a;
    --surface: #f4f5f9;
    --row: #ffffff;
    --ink: #3a3d44;
    --ink-strong: #2f3238;
    --muted: #5e6470;
    --line: #dde0e8;
  }
  * { box-sizing: border-box; margin: 0; padding: 0; }
  html, body { width: 1200px; height: 1081px; overflow: hidden; }
  body {
    background: var(--stage);
    font-family: "Roboto", sans-serif;
    color: var(--ink);
    position: relative;
  }
  .screen {
    position: absolute;
    left: 114px;
    width: 972px;
    height: 409px;
    background: var(--surface);
    box-shadow: 0 6px 18px rgba(40, 50, 100, 0.18);
  }
  .screen--models { top: 105px; }
  .screen--factors { top: 577px; }

  .topbar {
    height: 36px;
    background: var(--navy);
    position: relative;
    color: #fff;
  }
  .brand {
    position: absolute; left: 78px; top: 0; line-height: 36px;
    font-size: 15px; font-weight: 500; letter-spacing: 0.2px;
  }
  .tabs { position: absolute; left: 216px; top: 0; display: flex; height: 36px; }
  .tab { font-size: 11px; font-weight: 500; line-height: 36px; padding: 0 8px 0 0; }
  .tab--active { background: var(--lime); width: 56px; text-align: center; padding: 0; margin-right: 18px; }
  .nav { position: absolute; right: 77px; top: 0; display: flex; gap: 20px; height: 36px; align-items: center; }
  .nav-item { display: flex; align-items: center; gap: 3px; font-size: 11px; font-weight: 500; }
  .nav-item svg { width: 11px; height: 11px; fill: #fff; }

  .filters { position: absolute; top: 64px; left: 77px; right: 77px; height: 23px; }
  .filter-label {
    position: absolute; top: 0; line-height: 23px;
    font-size: 10.5px; font-weight: 500; color: var(--ink-strong);
  }
  .filter-input {
    position: absolute; top: 0; height: 23px; background: #fff;
    border: 1px solid var(--line); font-size: 10px; line-height: 21px;
    padding-left: 7px; color: var(--muted);
  }
  .export {
    position: absolute; right: 0; top: 0; width: 88px; height: 23px;
    background: var(--lime); color: #fff; font-size: 10.5px; font-weight: 500;
    display: flex; align-items: center; justify-content: center; gap: 3px;
  }
  .export svg { width: 10px; height: 10px; fill: #fff; }

  .table { position: absolute; left: 77px; width: 817px; top: 125px; }
  .tr { display: grid; align-items: center; padding-left: 14px; font-size: 9.5px; }
  .table--models .tr { grid-template-columns: 51px 117px 68px 74px 59px 54px 51px 55px 57px 55px 57px 56px 49px; }
  .table--factors .tr { padding-left: 17px; grid-template-columns: 79px 87px 138px 85px 87px 87px 86px 87px 64px; }
  .thead { height: 17px; font-weight: 500; font-size: 9.5px; color: var(--ink-strong); margin-bottom: 10px; }
  .tbody .tr { height: 30px; background: var(--row); margin-bottom: 4px; }
  .tbody .tr:first-child { background: linear-gradient(#ffffff 55%, #eceef2); }
  .tbody .tr.is-hover { box-shadow: 0 3px 12px rgba(40, 50, 80, 0.16); position: relative; }

  .footer {
    position: absolute; top: 368px; left: 0; right: 0; text-align: center;
    font-size: 11px; color: var(--muted);
  }
  .footer .sep { margin: 0 12px; }
</style>
</head>
<body>

<svg width="0" height="0" style="position:absolute">
  <defs>
    <symbol id="ico-home" viewBox="0 0 12 12"><path d="M6 1 0.5 6h1.6v5h3V8h1.8v3h3V6h1.6z"/></symbol>
    <symbol id="ico-gear" viewBox="0 0 12 12"><path d="M5 0.5h2l.3 1.5 1.2.6 1.3-.8 1.4 1.4-.8 1.3.6 1.2 1.5.3v2l-1.5.3-.6 1.2.8 1.3-1.4 1.4-1.3-.8-1.2.6L7 11.5H5l-.3-1.5-1.2-.6-1.3.8-1.4-1.4.8-1.3-.6-1.2L.5 7V5l1.5-.3.6-1.2-.8-1.3 1.4-1.4 1.3.8 1.2-.6zM6 4a2 2 0 1 0 0 4 2 2 0 1 0 0-4z" fill-rule="evenodd"/></symbol>
    <symbol id="ico-heart" viewBox="0 0 12 12"><path d="M6 11 1.2 6.2A3 3 0 0 1 6 2.3a3 3 0 0 1 4.8 3.9z"/></symbol>
    <symbol id="ico-upload" viewBox="0 0 12 12"><path d="M6 0.5 2.5 4h2.2v4h2.6V4h2.2zM0.8 8.5h2v1.5h6.4V8.5h2v3H.8z"/></symbol>
  </defs>
</svg>

<!-- Models screen -->
<section class="screen screen--models">
  <header class="topbar">
    <div class="brand">PELLWORTH</div>
    <div class="tabs"><span class="tab tab--active">250D</span><span class="tab">830</span><span class="tab">420</span></div>
    <nav class="nav">
      <span class="nav-item"><svg><use href="#ico-home"/></svg>MODELS</span>
      <span class="nav-item"><svg><use href="#ico-gear"/></svg>SENSITIVITIES</span>
      <span class="nav-item"><svg><use href="#ico-heart"/></svg>FAVOURITES</span>
    </nav>
  </header>
  <div class="filters">
    <span class="filter-label" style="left:0">Quality Threshold:</span>
    <span class="filter-input" style="left:94px;width:138px">-10</span>
    <span class="filter-label" style="left:265px">Abs. Size&nbsp; Thershold:</span>
    <span class="filter-input" style="left:375px;width:138px">-10</span>
    <span class="export"><svg><use href="#ico-upload"/></svg>EXPORT</span>
  </div>
  <div class="table table--models">
    <div class="tr thead"><span>ID</span><span>SECTOR</span><span>DATE</span><span>TIME</span><span>QUALITY</span><span>STAT 1</span><span>STAT 2</span><span>STAT 3</span><span>STAT 4</span><span>STAT 5</span><span>STAT 6</span><span>STAT 7</span><span>STAT 8</span></div>
    <div class="tbody">
      <div class="tr"><span>Model 1</span><span>Materials</span><span>2019-07-03</span><span>12:15:00.000</span><span>30.2288</span><span>2.01574</span><span>23.305</span><span>-0.149368</span><span>22.3054</span><span>4.63714</span><span>0.945706</span><span>2.81949</span><span>2.60858</span></div>
      <div class="tr is-hover"><span>Model 2</span><span>Industrials</span><span>2019-07-03</span><span>12:15:00.000</span><span>32.8694</span><span>0.87307</span><span>32.185</span><span>-0.033927</span><span>33.9911</span><span>11.5693</span><span>-0.472968</span><span>-0.830458</span><span>6.80646</span></div>
      <div class="tr"><span>Model 3</span><span>Consumer Discretionary</span><span>2019-07-03</span><span>12:15:00.000</span><span>30.2288</span><span>-0.569222</span><span>159.814</span><span>0.025228</span><span>172.616</span><span>10.2875</span><span>-0.750396</span><span>-0.385309</span><span>4.69146</span></div>
      <div class="tr"><span>Model 4</span><span>Information Technology</span><span>2019-07-03</span><span>12:15:00.000</span><span>45.6856</span><span>0.412148</span><span>202.488</span><span>0.084232</span><span>205.834</span><span>11.9094</span><span>-0.137913</span><span>0.449595</span><span>3.85106</span></div>
      <div class="tr"><span>Model 5</span><span>Information Technology</span><span>2019-07-03</span><span>12:15:00.000</span><span>75.7733</span><span>7.06728</span><span>188.605</span><span>0.016913</span><span>181.665</span><span>3.82241</span><span>0.981019</span><span>1.29847</span><span>3.34927</span></div>
    </div>
  </div>
  <footer class="footer">Copyrights © 2019 Pellworth Engines.&nbsp; All Rights Reserved<span class="sep">|</span>Privacy Policy<span class="sep">|</span>Terms Of Use.</footer>
</section>

<!-- Factors screen -->
<section class="screen screen--factors">
  <header class="topbar">
    <div class="brand">PELLWORTH</div>
    <div class="tabs"><span class="tab tab--active">250D</span><span class="tab">830</span><span class="tab">420</span></div>
    <nav class="nav">
      <span class="nav-item"><svg><use href="#ico-home"/></svg>MODELS</span>
      <span class="nav-item"><svg><use href="#ico-gear"/></svg>SENSITIVITIES</span>
      <span class="nav-item"><svg><use href="#ico-heart"/></svg>FAVOURITES</span>
    </nav>
  </header>
  <div class="filters">
    <span class="filter-label" style="left:0">Star 1 Threshold:</span>
    <span class="filter-input" style="left:94px;width:114px">-10</span>
    <span class="filter-label" style="left:224px">Star 1 Threshold:</span>
    <span class="filter-input" style="left:319px;width:114px">-10</span>
    <span class="filter-label" style="left:448px">Star 1 Threshold:</span>
    <span class="filter-input" style="left:542px;width:114px">-10</span>
    <span class="export"><svg><use href="#ico-upload"/></svg>EXPORT</span>
  </div>
  <div class="table table--factors" style="top:130px">
    <div class="tr thead"><span>FACTOR</span><span>ID</span><span>SECTOR</span><span>STAT 1</span><span>STAT 2</span><span>STAT 4</span><span>STAT 3</span><span>STAT 5</span><span>STAT 6</span></div>
    <div class="tbody">
      <div class="tr"><span>Factor 1</span><span>Model 1</span><span>Materials</span><span>-1.4</span><span>0.1</span><span>-3.1</span><span>0.7</span><span>30.2</span><span>0.9</span></div>
      <div class="tr is-hover"><span>Factor 2</span><span>Model 2</span><span>Materials</span><span>2.8</span><span>0.1</span><span>6.1</span><span>100</span><span>30.2</span><span>0.9</span></div>
      <div class="tr"><span>Factor 3</span><span>Model 3</span><span>Materials</span><span>-3.7</span><span>2.7</span><span>-7.2</span><span>100</span><span>30.2</span><span>0.9</span></div>
      <div class="tr"><span>Factor 1</span><span>Model 4</span><span>Industrials</span><span>2.8</span><span>0.2</span><span>2.7</span><span>0.5</span><span>30.2</span><span>-0.5</span></div>
      <div class="tr"><span>Factor 2</span><span>Model 5</span><span>Industrials</span><span>0.8</span><span>0.3</span><span>2.5</span><span>0.5</span><span>30.2</span><span>-0.5</span></div>
    </div>
  </div>
  <footer class="footer">Copyrights © 2019 Pellworth Engines.&nbsp; All Rights Reserved<span class="sep">|</span>Privacy Policy<span class="sep">|</span>Terms Of Use.</footer>
</section>

</body>
</html>
```